Communication and Marketing agency needs a new presentation card

We are a group of communication and marketing agencies specialized in companies that are in the logistics and industrial sector. The head agency is TELVANO Grupo and the group consists of 4 agencies: TELVANO Media, TELVANO Digital, TELVANO Research and DifundeEnPantalla. We hace 4 offices in Spain (Madrid, Barcelona, Valencia and Murcia). We are looking for a clean and attractive design that transmits our experience, brand presence in the market and knowledge to those who receive the card.It has to maintain the colors of the logo that is attached.
Target Market(s)
logistics and industrial sector
Marketing department
Contact Information for Business Card
Clean and attractive design

```html
<!DOCTYPE html>
<html lang="en">
<head>
<meta charset="utf-8">
<title>TELVANO Grupo – Business Card</title>
<link rel="stylesheet" href="https://fonts.googleapis.com/css2?family=Montserrat:wght@400;500;800&display=swap">
<style>
  :root {
    --brand-red: #b11f2b;
    --brand-grey: #54504e;
    --ink-grey: #6a6664;
    --paper: #ffffff;
    --backdrop: #d9dadc;
  }
  * { box-sizing: border-box; margin: 0; padding: 0; }
  html, body {
    width: 1200px; height: 960px; overflow: hidden;
    background: var(--backdrop);
    font-family: "Montserrat", Arial, sans-serif;
  }
  .sheet {
    position: relative; width: 1200px; height: 960px;
    display: flex; flex-direction: column; align-items: center; justify-content: center; gap: 48px;
  }
  .card {
    position: relative; width: 700px; height: 400px; overflow: hidden;
    box-shadow: 0 8px 24px rgba(0,0,0,.18);
  }

  /* Back side */
  .card-back { background: var(--brand-grey); color: var(--paper); }
  .agency-grid {
    position: absolute; left: 50%; top: 50%; transform: translate(-50%, -50%);
    display: grid; grid-template-columns: auto auto; column-gap: 56px; row-gap: 30px;
  }
  .agency-name {
    font-weight: 500; font-size: 24px; letter-spacing: 1px; color: var(--paper);
    white-space: nowrap;
  }

  /* Front side */
  .card-front { background: var(--paper); }
  .card-bands { position: absolute; inset: 0; }
  .brand-name {
    position: absolute; right: 56px; top: 78px;
    font-weight: 500; font-size: 34px; letter-spacing: 2px; color: var(--brand-red);
  }
  .person { position: absolute; left: 74px; top: 150px; }
  .person-name { font-weight: 800; font-size: 30px; color: var(--brand-red); line-height: 1.1; }
  .person-title { font-weight: 400; font-size: 18px; color: var(--ink-grey); margin-top: 2px; }
  .address {
    position: absolute; left: 112px; top: 236px;
    font-size: 17px; line-height: 1.25; color: var(--ink-grey);
  }
  .contact-list {
    position: absolute; left: 150px; top: 296px; list-style: none;
    font-size: 17px; line-height: 1.3; color: var(--ink-grey);
  }
  .contact-list li { display: flex; align-items: center; gap: 10px; }
  .contact-icon { width: 16px; height: 16px; flex: none; }
</style>
</head>
<body>
<main class="sheet">

  <section class="card card-back" aria-label="Business card back">
    <div class="agency-grid">
      <span class="agency-name">TELVANO Media</span>
      <span class="agency-name">TELVANO Digital</span>
      <span class="agency-name">TELVANO Research</span>
      <span class="agency-name">DifundeEnPantalla</span>
    </div>
  </section>

  <section class="card card-front" aria-label="Business card front">
    <svg class="card-bands" width="700" height="400" viewBox="0 0 700 400" aria-hidden="true">
      <polygon points="0,150 40,170 0,200" fill="var(--brand-grey)"/>
      <polygon points="0,360 700,360 700,400 0,400" fill="var(--brand-grey)"/>
      <polygon points="440,322 700,322 700,360 444,360" fill="var(--brand-grey)"/>
      <polygon points="452,318 660,318 700,336 700,356 458,356" fill="var(--brand-red)"/>
      <polygon points="662,318 700,318 700,334" fill="var(--brand-grey)"/>
    </svg>

    <div class="brand-name">TELVANO Grupo</div>

    <div class="person">
      <div class="person-name">Your Name</div>
      <div class="person-title">Your Title</div>
    </div>

    <address class="address" style="font-style:normal">
      Your address, city<br>state, ZIP 0000
    </address>

    <ul class="contact-list">
      <li>
        <svg class="contact-icon" viewBox="0 0 16 16" aria-hidden="true"><path d="M3 1l3 3-1.5 2c1 2 3 4 5 5L11.5 9.5l3 3L12 15C6 14 2 10 1 4z" fill="var(--brand-red)"/></svg>
        123-456-2100
      </li>
      <li>
        <svg class="contact-icon" viewBox="0 0 16 16" aria-hidden="true"><rect x="1" y="3" width="14" height="10" fill="var(--brand-red)"/><path d="M1 3l7 6 7-6" stroke="#fff" stroke-width="1.2" fill="none"/></svg>
        youremail@mailbox.com
      </li>
      <li>
        <svg class="contact-icon" viewBox="0 0 16 16" aria-hidden="true"><circle cx="8" cy="8" r="7" fill="var(--brand-red)"/><circle cx="8" cy="8" r="3" fill="none" stroke="#fff" stroke-width="1.2"/><path d="M1 8h14M8 1v14" stroke="#fff" stroke-width="1"/></svg>
        www.yourwebsite.com
      </li>
    </ul>
  </section>

</main>
</body>
</html>
```